Private Investment Firm Needs PowerPoint Presentation Template

Design PowerPoint template, take Pinebrook-submitted rough presentation draft, and drop it into new template. See attached Project Brief file for more detail.
Updates

Some decent designs have been submitted but they seem to lack the understanding of our target markets. I am hopeful that more time and feedback will result in better results.

Target Market(s)

Private company owners and intermediaries.

Font styles to use
Serif

Colors
3176b5

Requirements
Must have
• See attached Project Brief.
Nice to have
Should not have
• No B2C fluff--this is a B2B project.

```html
<!DOCTYPE html>
<html lang="en">
<head>
<meta charset="utf-8">
<title>Contact – Pinebrook Capital</title>
<link href="https://fonts.googleapis.com/css2?family=Montserrat:wght@400;600&family=Libre+Baskerville&display=swap" rel="stylesheet">
<style>
  :root {
    --brand-blue: #1a70c0;
    --band-blue: #1b74c2;
    --text-gray: #555a60;
    --paper: #ffffff;
    --glass-light: #eef1f4;
    --glass-mid: #d6dde4;
    --suit-dark: #1f2633;
    --suit-mid: #3a4455;
  }
  * { margin: 0; padding: 0; box-sizing: border-box; }
  html, body { width: 1200px; height: 676px; overflow: hidden; background: var(--paper); }
  .slide {
    position: relative; width: 1200px; height: 676px; overflow: hidden;
    background: var(--paper);
    font-family: "Montserrat", Arial, sans-serif;
    color: var(--text-gray);
  }
  .side-band { position: absolute; left: 0; top: 0; width: 44px; height: 676px; background: var(--band-blue); }
  .edge-band { position: absolute; right: 0; top: 0; width: 12px; height: 676px; background: var(--band-blue); }
  .side-url {
    position: absolute; left: 22px; top: 336px;
    transform: translate(-50%, -50%) rotate(-90deg);
    font-family: "Libre Baskerville", Georgia, serif;
    font-size: 15px; color: var(--paper); white-space: nowrap;
  }
  .page-number {
    position: absolute; right: 20px; top: 18px;
    font-family: "Libre Baskerville", Georgia, serif;
    font-size: 17px; color: #222;
  }
  .slide-title {
    position: absolute; left: 86px; top: 80px;
    font-size: 29px; font-weight: 600; color: var(--brand-blue); letter-spacing: 0.5px;
  }
  .office { position: absolute; left: 86px; }
  .office--boston { top: 178px; }
  .office--sf { top: 302px; }
  .office-name { font-size: 22px; font-weight: 600; color: var(--brand-blue); line-height: 30px; }
  .office-line { font-size: 17px; line-height: 24px; }
  .building-backdrop {
    position: absolute; left: 600px; top: 330px; width: 588px; height: 346px;
    background: linear-gradient(100deg, rgba(255,255,255,0) 0%, var(--glass-light) 45%, var(--glass-mid) 100%);
  }
  .portrait {
    position: absolute; left: 782px; top: 176px; width: 352px; height: 500px;
    border-radius: 120px 120px 0 0;
    background: linear-gradient(180deg, var(--suit-mid) 0%, var(--suit-dark) 60%);
  }
  .person {
    position: absolute; right: 491px; top: 438px; text-align: right;
  }
  .person-name { font-size: 24px; font-weight: 600; color: var(--brand-blue); line-height: 32px; margin-bottom: 4px; }
  .person-line { font-size: 16px; line-height: 22.4px; }
  .person-email { border-bottom: 1px solid #b8bdc2; }
  .brand {
    position: absolute; left: 68px; top: 612px;
    display: flex; align-items: center; gap: 10px;
  }
  .brand-dot { width: 36px; height: 36px; border-radius: 50%; background: var(--brand-blue); }
  .brand-name { font-size: 17px; font-weight: 600; color: var(--brand-blue); }
  .copyright {
    position: absolute; left: 322px; top: 631px;
    font-size: 11.5px; color: var(--text-gray);
  }
</style>
</head>
<body>
<main class="slide">
  <div class="side-band"></div>
  <div class="edge-band"></div>
  <div class="side-url">www.pinebrookcapital.com</div>
  <div class="page-number">25</div>

  <h1 class="slide-title">CONTACT</h1>

  <section class="office office--boston">
    <h2 class="office-name">Boston Office</h2>
    <p class="office-line">40 Harbor View Road, Suite 210</p>
    <p class="office-line">Lynnfield, MA 01940</p>
    <p class="office-line">(617) 555-0140</p>
  </section>

  <section class="office office--sf">
    <h2 class="office-name">San Francisco Office</h2>
    <p class="office-line">Two Market Plaza, Suite 480</p>
    <p class="office-line">San Francisco, CA 94105</p>
    <p class="office-line">(415) 555-0182</p>
  </section>

  <div class="building-backdrop" role="img" aria-label="Soft photo of a modern glass office building"></div>
  <div class="portrait" role="img" aria-label="Portrait of the principal in a dark blazer and blue shirt, arms crossed"></div>

  <section class="person">
    <h2 class="person-name">Jonathan R. Marlowe</h2>
    <p class="person-line">Principal</p>
    <p class="person-line">210 Millbrook Lane, Suite 140</p>
    <p class="person-line">Ridgefield, CT&nbsp; 06877</p>
    <p class="person-line">Direct: (617) 555-0163</p>
    <p class="person-line"><span class="person-email">jmarlowe@pinebrookcapital.com</span></p>
  </section>

  <div class="brand">
    <span class="brand-dot"></span>
    <span class="brand-name">Pinebrook Capital</span>
  </div>

  <p class="copyright">Copyright © 2018 ◆ Pinebrook Capital Partners ◆ All Rights Reserved</p>
</main>
</body>
</html>
```